sydney wedding photography business needs a business card design

we need a business card design for a sydney based wedding photography and videography business. our business name is :golden hour studio and film. our target clients are 24-35 yrs female. our style is candid, organic, natural, dynamic. we are a team of young photographers and videographers, and help brides to create memories that they will cherish for the rest of their lives. the logo will be provided. we want an elegant design that reflects our style, and also want to give a great impression to our clients that we are one of the best studios in sydney and our brand means quality and premium service.

Target Market(s)

bride to be, 24-35 years old, living in sydney and surrunding areas

Industry/Entity Type

Wedding Photography

Contact Information for Business Card

address: 57 tarrant street, glenmore nsw 2047
mobile: 0431872259
phone: (02) 9163 2408
info@tidewillowstudio.net.au
www.tidewillowstudio.net.au
facebook:tidewillowweddings
instagram:tidewillowweddings

Font styles to use
Serif
Sans Serif

Requirements
Nice to have
• maybe add my slogan"moments forever treasured" if the layout looks good
Should not have
• no black color, not good idea for wedding biz card

```html
<!DOCTYPE html>
<html lang="en">
<head>
<meta charset="utf-8">
<title>Golden Hour Studio and Film – Business Card</title>
<link rel="stylesheet" href="https://fonts.googleapis.com/css2?family=Josefin+Sans:wght@300;400;600&display=swap">
<style>
  :root {
    --stage: #3d3b39;
    --card: #ffffff;
    --gold: #b8862f;
    --gold-light: #d9a640;
    --bronze: #7a4f1c;
    --ink: #2e2b28;
    --rule: #55514c;
    --ring: #e6e6e6;
    --gem-a: #f3f3f3;
    --gem-b: #e2e2e2;
  }
  * { margin: 0; padding: 0; box-sizing: border-box; }
  html, body { width: 1200px; height: 900px; overflow: hidden; }
  body {
    background: var(--stage);
    font-family: "Josefin Sans", sans-serif;
    color: var(--ink);
    position: relative;
  }
  .card {
    position: absolute;
    top: 301px;
    width: 514px;
    height: 296px;
    background: var(--card);
    overflow: hidden;
  }
  .card--front { left: 72px; }
  .card--back { left: 615px; }

  /* front */
  .front__arc { position: absolute; left: 410px; top: -50px; }
  .front__gem {
    position: absolute; left: 0; top: 190px; width: 100px; height: 106px;
    background: radial-gradient(ellipse at 40% 40%, var(--gem-a), var(--gem-b) 70%, transparent 72%);
  }
  .brand-frame {
    position: absolute; left: 103px; top: 106px; width: 311px; height: 84px;
    border: 1.5px solid var(--gold);
    display: flex; flex-direction: column; align-items: center; justify-content: center;
  }
  .brand-name {
    color: var(--gold); font-weight: 400; text-align: center; line-height: 1;
  }
  .brand-name__main { display: block; font-size: 34px; }
  .brand-name__sub { display: block; font-size: 13px; letter-spacing: 0.42em; margin-top: 8px; padding-left: 0.42em; }
  .slogan {
    position: absolute; left: 101px; top: 205px; width: 314px;
    font-size: 12px; letter-spacing: 0.36em; white-space: nowrap; text-align: center;
  }
  .slogan__first { color: var(--bronze); }
  .slogan__rest { color: var(--gold-light); }

  /* back */
  .back__brand { position: absolute; left: 0; top: 44px; width: 100%; }
  .back__brand .brand-name__main { font-size: 36px; }
  .back__brand .brand-name__sub { font-size: 12px; margin-top: 9px; }
  .rule { position: absolute; left: 34px; width: 446px; height: 1px; background: var(--rule); }
  .rule--top { top: 142px; }
  .rule--bottom { top: 232px; }
  .services {
    position: absolute; left: 34px; top: 156px; width: 446px;
    font-size: 12.5px; font-weight: 300; letter-spacing: 0.42em; text-align: center; white-space: nowrap;
  }
  .icon-row { position: absolute; left: 34px; top: 170px; width: 446px; height: 14px; }
  .contact {
    position: absolute; top: 192px; font-size: 12.5px; line-height: 18px;
    text-align: center; white-space: nowrap; font-weight: 300;
  }
  .contact--address { left: 99px; transform: translateX(-50%); }
  .contact--phone { left: 237px; transform: translateX(-50%); }
  .contact--web { left: 394px; transform: translateX(-50%); font-size: 11.5px; }
  .footer-row {
    position: absolute; top: 247px; font-size: 11.5px; display: flex; align-items: center; gap: 7px;
    white-space: nowrap; font-weight: 300;
  }
  .footer-row--person { left: 50px; }
  .footer-row--social { right: 34px; }
  .dot { width: 14px; height: 14px; border-radius: 50%; background: var(--gold); display: inline-block; }
</style>
</head>
<body>
  <section class="card card--front" aria-label="Card front">
    <svg class="front__arc" width="170" height="170" viewBox="0 0 170 170" aria-hidden="true">
      <circle cx="85" cy="85" r="72" fill="none" stroke="var(--ring)" stroke-width="12"/>
    </svg>
    <div class="front__gem" role="img" aria-label="Faint diamond ring decoration"></div>
    <div class="brand-frame">
      <p class="brand-name">
        <span class="brand-name__main">Golden Hour</span>
        <span class="brand-name__sub">STUDIO AND FILM</span>
      </p>
    </div>
    <p class="slogan"><span class="slogan__first">MOMENTS</span> <span class="slogan__rest">FOREVER TREASURED</span></p>
  </section>

  <section class="card card--back" aria-label="Card back">
    <div class="back__brand">
      <p class="brand-name">
        <span class="brand-name__main">Golden Hour</span>
        <span class="brand-name__sub">STUDIO AND FILM</span>
      </p>
    </div>
    <div class="rule rule--top"></div>
    <p class="services">WEDDING | ENGAGEMENT | FAMILY</p>
    <svg class="icon-row" width="446" height="14" viewBox="0 0 446 14" aria-hidden="true">
      <g stroke="var(--rule)" stroke-width="1">
        <line x1="0" y1="7" x2="55" y2="7"/><line x1="75" y1="7" x2="193" y2="7"/>
        <line x1="214" y1="7" x2="354" y2="7"/><line x1="374" y1="7" x2="446" y2="7"/>
      </g>
      <path d="M65 1a5 5 0 0 1 5 5c0 4-5 8-5 8s-5-4-5-8a5 5 0 0 1 5-5z" fill="var(--gold)"/>
      <circle cx="65" cy="6" r="1.8" fill="#fff"/>
      <path d="M197 9c0-5 13-5 13 0l-3 2-2-2h-3l-2 2z" fill="var(--gold)"/>
      <circle cx="364" cy="7" r="6" fill="var(--gold)"/>
      <g stroke="#fff" stroke-width="0.8" fill="none">
        <ellipse cx="364" cy="7" rx="2.5" ry="6"/><line x1="358" y1="7" x2="370" y2="7"/>
      </g>
    </svg>
    <p class="contact contact--address">57 tarrant street<br>glenmore nsw 2047</p>
    <p class="contact contact--phone">0431 872 259<br>(02) 9163 2408</p>
    <p class="contact contact--web">info@tidewillowstudio.net.au<br>www.tidewillowstudio.net.au</p>
    <div class="rule rule--bottom"></div>
    <p class="footer-row footer-row--person">
      <svg width="14" height="14" viewBox="0 0 14 14" aria-hidden="true">
        <circle cx="7" cy="7" r="7" fill="var(--gold)"/>
        <circle cx="7" cy="5.3" r="2.3" fill="#fff"/>
        <path d="M3 11.5c0-3 8-3 8 0" fill="#fff"/>
      </svg>
      DANIEL HSU
    </p>
    <p class="footer-row footer-row--social"><span class="dot"></span>tidewillowweddings</p>
  </section>
</body>
</html>
```